real esate business card with company logo and name

we need a business card design for a real esate company

The company name is Walsh & Brand Pty Ltd, and we have our logo designed and will upload. We want classic or moden feel. Black or white background. looks more textured. Should include folowinginformations
Owen Walsh and Lucy Brand
Sales Agents & Onsite Manager
p: 07 5948 2063
F: 07 5948 2174
M:0431 857 219
3/42 Marlow Crescent, FERNLEA QLD 4213

We want this business card looks professonal. Thank you in advance.

Industry/Entity Type

Real Estate Agent

Contact Information for Business Card

Owen Walsh and Lucy Brand
Onsite Manager & Sales Agents
p: 07 5948 2063
M:0431 857 219

Font styles to use
Serif

Colors
000000
fbfbfb
333333
959595

Requirements
Must have
• company logo and name, black or white back ground

```html
<!DOCTYPE html>
<html lang="en">
<head>
<meta charset="utf-8">
<title>Walsh &amp; Brand Pty Ltd – Business Card</title>
<link rel="stylesheet" href="https://fonts.googleapis.com/css2?family=Open+Sans:wght@300;400&display=swap">
<style>
  :root {
    --page-bg: #e9e9e9;
    --card-white: #fbfbfb;
    --card-edge: #e4e4e4;
    --band-light: #d4d4d4;
    --band-mid: #a9a9a9;
    --band-dark: #8f8f8f;
    --panel-top: #777777;
    --panel-bottom: #5e5e5e;
    --text-light: #fbfbfb;
    --brand-grey: #959595;
    --ink-dark: #333333;
  }
  * { box-sizing: border-box; margin: 0; padding: 0; }
  html, body {
    width: 1200px;
    height: 892px;
    overflow: hidden;
    background: var(--page-bg);
    font-family: "Open Sans", Arial, sans-serif;
  }
  .business-card {
    position: absolute;
    left: 110px;
    top: 166px;
    width: 980px;
    height: 560px;
    border-radius: 34px;
    overflow: hidden;
    background: linear-gradient(120deg, var(--card-white) 0%, #f1f1f1 60%, var(--card-edge) 100%);
    box-shadow: 0 10px 30px rgba(0,0,0,0.18);
  }
  .band-light {
    position: absolute;
    left: 430px;
    top: 0;
    width: 400px;
    height: 100%;
    background: linear-gradient(90deg, #e0e0e0, var(--band-light));
  }
  .band-edge {
    position: absolute;
    left: 830px;
    top: 0;
    width: 150px;
    height: 100%;
    background: linear-gradient(90deg, var(--band-mid), var(--band-dark));
  }
  .brand {
    position: absolute;
    left: 60px;
    top: 330px;
    width: 350px;
    display: flex;
    align-items: center;
    gap: 14px;
  }
  .brand-square {
    flex: none;
    width: 28px;
    height: 28px;
    background: var(--brand-grey);
  }
  .brand-name {
    font-size: 21px;
    font-weight: 400;
    color: var(--brand-grey);
    letter-spacing: 0.5px;
    text-transform: uppercase;
    white-space: nowrap;
  }
  .contact-panel {
    position: absolute;
    left: 460px;
    top: 56px;
    width: 470px;
    height: 448px;
    border-radius: 18px;
    background: linear-gradient(160deg, var(--panel-top), var(--panel-bottom));
    color: var(--text-light);
    padding: 40px 20px 0 34px;
  }
  .agent-names {
    font-size: 30px;
    font-weight: 400;
    line-height: 1.15;
    letter-spacing: -0.3px;
    white-space: nowrap;
  }
  .agent-role {
    font-size: 21px;
    font-weight: 300;
    margin-top: 6px;
  }
  .contact-list {
    list-style: none;
    margin-top: 90px;
    font-size: 22px;
    font-weight: 300;
    line-height: 1.35;
  }
  .contact-list li {
    display: flex;
    align-items: flex-start;
    gap: 14px;
  }
  .contact-icon {
    flex: none;
    width: 24px;
    height: 24px;
    margin-top: 4px;
  }
  .address-line { display: block; }
</style>
</head>
<body>
  <div class="business-card">
    <div class="band-light"></div>
    <div class="band-edge"></div>

    <div class="brand">
      <span class="brand-square"></span>
      <span class="brand-name">Walsh &amp; Brand Pty Ltd.</span>
    </div>

    <div class="contact-panel">
      <h1 class="agent-names">Owen Walsh and Lucy Brand</h1>
      <p class="agent-role">Onsite Manager &amp; Sales Agents</p>

      <ul class="contact-list">
        <li>
          <svg class="contact-icon" viewBox="0 0 24 24" aria-hidden="true">
            <rect width="24" height="24" rx="3" fill="#fbfbfb"/>
            <path d="M7 5c1 0 2 2.5 2 3s-1 1-1 1.5c.5 2 2.5 4 4.5 4.5.5 0 1-1 1.5-1s3 1 3 2-1 3-2.5 3C9 18 6 15 6 7.5 6 6 6.5 5 7 5z" fill="#5e5e5e"/>
          </svg>
          <span>07 5948 2063</span>
        </li>
        <li>
          <svg class="contact-icon" viewBox="0 0 24 24" aria-hidden="true">
            <rect width="24" height="24" rx="3" fill="#fbfbfb"/>
            <rect x="8" y="4" width="8" height="16" rx="1.5" fill="#5e5e5e"/>
            <rect x="9.5" y="6" width="5" height="9" fill="#fbfbfb"/>
          </svg>
          <span>0431 857 219</span>
        </li>
        <li>
          <svg class="contact-icon" viewBox="0 0 24 24" aria-hidden="true">
            <rect width="24" height="24" rx="3" fill="#fbfbfb"/>
            <path d="M12 5l7 6h-2v7h-4v-4h-2v4H7v-7H5z" fill="#5e5e5e"/>
          </svg>
          <span>
            <span class="address-line">3/42 Marlow Crescent,</span>
            <span class="address-line">FERNLEA QLD 4213</span>
          </span>
        </li>
      </ul>
    </div>
  </div>
</body>
</html>
```